Business Cards for company that supports physicians that do medical research

Need to create a business card for Qorvel Studies (www.qorvelstudies.example), a company devoted to supporting physicians who conduct medical research. The form of the card should match the message of research and information quest. I have provided the logo of the company as an uploaded file. Designs should be simple and slick aimed at very high end clients.

Target Market(s)

Medical doctors that are also researchers

Industry/Entity Type

Medical

Contact Information for Business Card

Should feature logo and fields for personal info:
Name/title
Phone /email

Font styles to use
Serif
Sans Serif

Requirements
Must have
• Qorvel logo and fields for personal info:
• Name: Bertrand Okonfu
• Title: VP Research and Senior Analyst
• Phone: 555-203-4719
• email: info@qorvelstudies.example
Nice to have
• Interesting cards that I've seen:
• 1- all black/charcoal or very dark background
• 2- Plastic - semi-transparent
• 3- non-standard height-width ratios
• 4- Functional cards -- USB drive incorporated
Should not have
• Too busy; needs to stay very simple

```html
<!DOCTYPE html>
<html lang="en">
<head>
<meta charset="utf-8">
<title>Qorvel Studies – Business Card</title>
<link rel="stylesheet" href="https://fonts.googleapis.com/css2?family=Open+Sans:ital,wght@0,400;0,600;1,400&display=swap">
<style>
  :root {
    --backdrop: #3b3b3b;
    --card-white: #fbfbfb;
    --brand-blue: #1d7cbd;
    --brand-green: #4ab444;
    --ink-white: #ffffff;
  }
  html, body {
    margin: 0;
    padding: 0;
    width: 1200px;
    height: 750px;
    overflow: hidden;
    background: var(--backdrop);
    font-family: "Open Sans", Arial, sans-serif;
  }
  .canvas {
    position: relative;
    width: 1200px;
    height: 750px;
  }
  .card {
    position: absolute;
    top: 228px;
    width: 461px;
    height: 262px;
    overflow: hidden;
  }
  .card-front { left: 124px; background: var(--card-white); }
  .card-back  { left: 618px; background: var(--brand-green); }

  .info-band {
    position: absolute;
    left: 0;
    right: 0;
    bottom: 0;
    height: 132px;
    background: var(--brand-blue);
  }
  .info-rule {
    position: absolute;
    left: 0;
    right: 0;
    bottom: 132px;
    height: 4px;
    background: var(--brand-green);
  }

  .front-brand {
    position: absolute;
    right: 40px;
    top: 34px;
    text-align: right;
    color: var(--brand-green);
    font-weight: 600;
    line-height: 1;
  }
  .brand-name { display: block; font-size: 46px; letter-spacing: -1px; }
  .brand-sub {
    display: block;
    margin-top: 6px;
    font-size: 17px;
    letter-spacing: 6px;
  }

  .person {
    position: absolute;
    left: 20px;
    top: 146px;
    color: var(--ink-white);
  }
  .person-name { margin: 0; font-size: 16px; font-weight: 600; line-height: 1.3; }
  .person-title { margin: 2px 0 0 2px; font-size: 12px; }
  .contacts {
    list-style: none;
    margin: 10px 0 0 2px;
    padding: 0;
    font-size: 11px;
  }
  .contacts li {
    display: flex;
    align-items: center;
    gap: 6px;
    height: 17.5px;
  }
  .contacts svg { width: 11px; height: 11px; fill: var(--ink-white); }

  .back-brand {
    position: absolute;
    left: 0;
    right: 0;
    top: 82px;
    text-align: center;
    color: var(--ink-white);
    font-weight: 600;
    line-height: 1;
  }
  .back-url {
    position: absolute;
    left: 0;
    right: 0;
    top: 216px;
    margin: 0;
    text-align: center;
    color: var(--ink-white);
    font-size: 11px;
    font-style: italic;
    letter-spacing: 3px;
  }
</style>
</head>
<body>
<div class="canvas">
  <section class="card card-front" aria-label="Business card front">
    <div class="info-rule"></div>
    <div class="info-band"></div>

    <div class="front-brand">
      <span class="brand-name">Qorvel</span>
      <span class="brand-sub">STUDIES</span>
    </div>

    <div class="person">
      <h1 class="person-name">Bertrand Okonfu</h1>
      <p class="person-title">VP Research &amp; Senior Analyst</p>
      <ul class="contacts">
        <li>
          <svg viewBox="0 0 24 24" aria-hidden="true"><path d="M6.6 10.8c1.4 2.8 3.8 5.1 6.6 6.6l2.2-2.2c.3-.3.7-.4 1-.2 1.1.4 2.3.6 3.6.6.6 0 1 .4 1 1V20c0 .6-.4 1-1 1C10.6 21 3 13.4 3 4c0-.6.4-1 1-1h3.5c.6 0 1 .4 1 1 0 1.3.2 2.5.6 3.6.1.3 0 .7-.2 1z"/></svg>
          <span>555-203-4719</span>
        </li>
        <li>
          <svg viewBox="0 0 24 24" aria-hidden="true"><path d="M2 5h20v14H2z M4 7v.5l8 5 8-5V7l-8 5z" fill-rule="evenodd"/></svg>
          <span>info@qorvelstudies.example</span>
        </li>
        <li>
          <svg viewBox="0 0 24 24" aria-hidden="true"><path d="M12 2a10 10 0 1 0 0 20 10 10 0 0 0 0-20zm-1 17.9A8 8 0 0 1 4.1 11H7c0 3 1.4 5.5 4 8.9zM13 19.9c2.6-3.4 4-5.9 4-8.9h2.9a8 8 0 0 1-6.9 8.9zM9 11h6c0 2.5-1.1 4.8-3 7.4C10.1 15.8 9 13.5 9 11zm-4.9-2A8 8 0 0 1 11 4.1 13 13 0 0 0 7 9zm4.9 0c.5-2 1.6-3.8 3-5.4 1.4 1.6 2.5 3.4 3 5.4zm8 0a13 13 0 0 0-4-4.9A8 8 0 0 1 19.9 9z"/></svg>
          <span>www.qorvelstudies.example</span>
        </li>
      </ul>
    </div>
  </section>

  <section class="card card-back" aria-label="Business card back">
    <div class="back-brand">
      <span class="brand-name">Qorvel</span>
      <span class="brand-sub">STUDIES</span>
    </div>
    <p class="back-url">www.qorvelstudies.example</p>
  </section>
</div>
</body>
</html>
```